Redesign of business card for Cedar Ridge Mechanical

We are looking for a new design for our business cards for Cedar Ridge Mechanical. We are a plumbing & HVAC construction company, operating on the West Coast of Canada and USA. Logo attached.
Industry/Entity Type
Construction - Plumbing & HVAC
Contact Information for Business Card
Name, address, phone numbers, email, website address
Look and feel
Each slider illustrates characteristics of the customer's brand and the style your logo design should communicate.

```html
<!DOCTYPE html>
<html lang="en">
<head>
<meta charset="utf-8">
<title>Cedar Ridge Mechanical – Business Card</title>
<link href="https://fonts.googleapis.com/css2?family=Montserrat:wght@300;400;700&display=swap" rel="stylesheet">
<style>
  :root {
    --backdrop: #2b2b2b;
    --ink: #0a0a0a;
    --paper: #ffffff;
    --muted: #3a3a3a;
  }
  * { box-sizing: border-box; margin: 0; padding: 0; }
  html, body {
    width: 1200px; height: 880px; overflow: hidden;
    background: var(--backdrop);
    font-family: "Montserrat", sans-serif;
  }
  .stage {
    position: relative; width: 1200px; height: 880px;
  }
  .card {
    position: absolute; left: 300px;
    width: 600px; height: 343px;
    border-radius: 26px;
  }
  .card-front { top: 60px; background: var(--ink); }
  .card-back { top: 470px; background: var(--paper); color: var(--ink); }

  .brand {
    position: absolute; display: flex; align-items: center; gap: 14px;
    font-weight: 700; text-transform: uppercase; letter-spacing: 0.06em;
  }
  .brand-mark { display: block; border: 5px solid currentColor; }
  .card-front .brand {
    color: var(--paper); left: 0; right: 0; top: 0; bottom: 0;
    justify-content: center; font-size: 26px;
  }
  .card-front .brand-mark { width: 44px; height: 44px; }
  .card-back .brand {
    right: 34px; top: 34px; font-size: 15px;
  }
  .card-back .brand-mark { width: 26px; height: 26px; border-width: 4px; }

  .person { position: absolute; left: 46px; top: 128px; }
  .person-name { font-size: 26px; font-weight: 700; letter-spacing: 0.02em; }
  .person-role { font-size: 16px; font-weight: 300; color: var(--muted); margin-top: 2px; }
  .accent-bar {
    position: absolute; left: 0; top: 134px;
    width: 28px; height: 56px; background: var(--ink);
  }

  .address {
    position: absolute; right: 34px; top: 150px;
    text-align: right; font-size: 15px; font-weight: 300; line-height: 1.5;
    color: var(--muted);
  }

  .contacts {
    position: absolute; left: 46px; bottom: 30px;
    list-style: none; font-size: 16px; font-weight: 400; line-height: 1.75;
  }
  .contacts li { display: flex; align-items: center; gap: 10px; }
  .contacts svg { width: 15px; height: 15px; fill: var(--ink); flex: none; }
</style>
</head>
<body>
<main class="stage">
  <section class="card card-front" aria-label="Card front">
    <div class="brand"><span class="brand-mark"></span>Cedar Ridge Mechanical</div>
  </section>

  <section class="card card-back" aria-label="Card back">
    <div class="brand"><span class="brand-mark"></span>Cedar Ridge Mechanical</div>

    <span class="accent-bar"></span>
    <div class="person">
      <h1 class="person-name">DANIEL HAYES</h1>
      <p class="person-role">Managing Director</p>
    </div>

    <address class="address" style="font-style:normal">
      Your address, City<br>State, Zip 1234
    </address>

    <ul class="contacts">
      <li>
        <svg viewBox="0 0 16 16" aria-hidden="true"><path d="M3 1h3l1.5 4-2 1.2a9 9 0 0 0 4.3 4.3L11 8.5l4 1.5v3a2 2 0 0 1-2 2A12 12 0 0 1 1 3a2 2 0 0 1 2-2z"/></svg>
        123 456 789
      </li>
      <li>
        <svg viewBox="0 0 16 16" aria-hidden="true"><path d="M1 3h14v10H1z M2 4.2v.3l6 4.3 6-4.3v-.3z" fill-rule="evenodd"/></svg>
        info@yourmail.com
      </li>
      <li>
        <svg viewBox="0 0 16 16" aria-hidden="true"><circle cx="8" cy="8" r="7"/><path d="M1 8h14M8 1c-3 3.5-3 10.5 0 14M8 1c3 3.5 3 10.5 0 14" stroke="#fff" stroke-width="1" fill="none"/></svg>
        www.yourwebsite.com
      </li>
    </ul>
  </section>
</main>
</body>
</html>
```